Dunmore Roofing

Want a professional looking business card

Industry/Entity Type

Business

Contact Information for Business Card

Paul Dunmore ( Owner) paul@dunmoreroofing-example.com, www.dunmoreroofing-example.com, Adress: 4172 Township road 43 Larkfield,ON K9X4T2

```html
<!DOCTYPE html>
<html lang="en">
<head>
<meta charset="utf-8">
<title>Dunmore Roofing – Business Card</title>
<link href="https://fonts.googleapis.com/css2?family=Roboto:wght@400;500;700&display=swap" rel="stylesheet">
<style>
  :root {
    --brand-blue: #1b4a8c;
    --brand-navy: #163f7a;
    --stripe-grey: #8c8f94;
    --text-grey: #5a5d62;
    --card-white: #ffffff;
    --stage: #e6e7e9;
  }
  * { box-sizing: border-box; margin: 0; padding: 0; }
  html, body { width: 1200px; height: 880px; overflow: hidden; }
  body {
    background: var(--stage);
    font-family: "Roboto", Arial, sans-serif;
    position: relative;
  }
  .card {
    position: absolute;
    left: 320px;
    width: 560px;
    height: 320px;
    border-radius: 16px;
    overflow: hidden;
    box-shadow: 0 8px 24px rgba(0,0,0,.18);
  }
  /* Front */
  .card-front { top: 80px; background: var(--brand-blue); color: var(--card-white); }
  .front-wordmark {
    position: absolute; left: 0; right: 0; top: 112px;
    display: flex; align-items: center; justify-content: center; gap: 14px;
  }
  .wordmark-square { width: 22px; height: 22px; background: var(--card-white); flex: none; }
  .front-wordmark .wordmark-text {
    font-weight: 700; font-size: 40px; letter-spacing: 2px; color: var(--card-white);
  }
  .front-website {
    position: absolute; left: 0; right: 0; top: 196px;
    text-align: center; font-size: 15px; letter-spacing: 1.2px;
  }
  /* Back */
  .card-back { top: 480px; background: var(--card-white); }
  .back-wordmark {
    position: absolute; left: 40px; top: 104px;
    display: flex; align-items: center; gap: 10px;
  }
  .back-wordmark .wordmark-square { background: var(--brand-blue); width: 18px; height: 18px; }
  .back-wordmark .wordmark-text {
    font-weight: 700; font-size: 28px; letter-spacing: 1px; color: var(--brand-blue); line-height: 1;
  }
  .holder { position: absolute; right: 36px; top: 118px; text-align: right; }
  .holder-name { font-weight: 500; font-size: 21px; color: var(--brand-navy); line-height: 1; }
  .holder-role { font-size: 13px; color: var(--text-grey); margin-top: 3px; line-height: 1; }
  .divider {
    position: absolute; left: 40px; right: 36px; top: 164px;
    height: 1.5px; background: var(--brand-navy);
  }
  .contacts { position: absolute; left: 40px; top: 190px; list-style: none; }
  .contacts li {
    display: flex; align-items: center; gap: 8px;
    font-size: 13.5px; color: var(--text-grey); line-height: 22px;
  }
  .contacts li .accent { color: var(--brand-navy); }
  .contact-icon {
    width: 16px; height: 16px; border-radius: 50%;
    background: var(--brand-blue); display: inline-flex;
    align-items: center; justify-content: center; flex: none;
  }
  .address {
    position: absolute; right: 36px; top: 184px;
    text-align: right; font-size: 14px; color: var(--text-grey); line-height: 19px;
  }
  .base-band { position: absolute; left: 0; bottom: 0; }
</style>
</head>
<body>

<section class="card card-front" aria-label="Business card front">
  <div class="front-wordmark">
    <span class="wordmark-square"></span>
    <span class="wordmark-text">DUNMORE ROOFING</span>
  </div>
  <p class="front-website">www.dunmoreroofing-example.com</p>
</section>

<section class="card card-back" aria-label="Business card back">
  <div class="back-wordmark">
    <span class="wordmark-square"></span>
    <span class="wordmark-text">DUNMORE ROOFING</span>
  </div>

  <div class="holder">
    <p class="holder-name">Paul Dunmore</p>
    <p class="holder-role">Owner</p>
  </div>
  <div class="divider"></div>

  <ul class="contacts">
    <li>
      <span class="contact-icon">
        <svg width="10" height="10" viewBox="0 0 10 10"><path d="M2 1.2 3.4 1l.8 2-1 .7a5 5 0 0 0 2.1 2.1l.7-1 2 .8-.2 1.4C6 7.2 2.8 4 2 1.2z" fill="#fff"/></svg>
      </span>
      (613) 555-0142
    </li>
    <li>
      <span class="contact-icon">
        <svg width="10" height="10" viewBox="0 0 10 10"><rect x="1.2" y="2.5" width="7.6" height="5" fill="none" stroke="#fff" stroke-width="1"/><path d="M1.2 2.5 5 5.4l3.8-2.9" fill="none" stroke="#fff" stroke-width="1"/></svg>
      </span>
      paul@dunmoreroofing-example.com
    </li>
    <li>
      <span class="contact-icon">
        <svg width="10" height="10" viewBox="0 0 10 10"><circle cx="5" cy="5" r="3.6" fill="none" stroke="#fff" stroke-width="1"/><ellipse cx="5" cy="5" rx="1.5" ry="3.6" fill="none" stroke="#fff" stroke-width=".8"/><path d="M1.4 5h7.2" stroke="#fff" stroke-width=".8"/></svg>
      </span>
      <span>www.<span class="accent">dunmoreroofing-example</span>.com</span>
    </li>
  </ul>

  <p class="address">4172 Township road 43,<br>Larkfield,ON K9X4T2</p>

  <svg class="base-band" width="560" height="80" viewBox="0 0 560 80" aria-hidden="true">
    <path d="M0 50 H408 L420 38 V30 L428 20 H560 V28 H432 L428 32 V42 L414 56 H0 Z" fill="var(--stripe-grey)"/>
    <path d="M0 62 H416 L432 46 V36 L438 30 H560 V80 H0 Z" fill="var(--brand-blue)"/>
  </svg>
</section>

</body>
</html>
```